Gulf Book About Father - need cover design named - الغيم

The book talks about the good father who teaches his sons high principles and values, to be successful people in their lives.

Book size - 15 cm high
21 cm width
Data on the cover:
Name of the Book: الغيم
Author: دكتور/ مازن بن وليد الحمداني- Just write the name without the word writer
1440-2018
Logo of the Publishing House

Target Market(s)

Book submitted to children - Families - Schools - Public libraries

Requirements
Must have
• Design must include one or all of these options:
• The first option: a picture that has a meaning for a father who has values and principles with the son or children, expresses the contradiction - education, etc. -
• The background is to express the tender love or taken from the Emirates flag
• The second option: abstract art - with a background taken from the colors of the flag of the Emirates - or colors about love and tenderness
Should not have
• direct image

```html
<!DOCTYPE html>
<html lang="ar" dir="rtl">
<head>
<meta charset="utf-8">
<title>الغيم — غلاف كتاب</title>
<link rel="stylesheet" href="https://fonts.googleapis.com/css2?family=Cairo:wght@700;900&display=swap">
<style>
  :root {
    --brown: #673617;
    --orange: #d2692c;
    --paper: #f9fbfc;
    --blush-light: #fbebe4;
    --blush: #eec6b8;
    --blush-deep: #d49a8a;
    --white: #ffffff;
  }
  * { margin: 0; padding: 0; box-sizing: border-box; }
  html, body { width: 938px; height: 1200px; overflow: hidden; background: var(--paper); }
  body { font-family: "Cairo", sans-serif; }

  .cover { position: relative; width: 938px; height: 1200px; overflow: hidden; }

  .title-band {
    position: absolute; inset: 0 0 auto 0; height: 411px;
    background: var(--paper);
    box-shadow: 0 6px 10px rgba(120, 70, 50, 0.18);
    z-index: 2;
  }
  .title-band svg { position: absolute; inset: 0; }

  .cover-art {
    position: absolute; top: 411px; left: 0; right: 0; height: 633px;
    background:
      radial-gradient(ellipse 40% 35% at 55% 45%, var(--white) 0%, rgba(255,255,255,0) 70%),
      linear-gradient(110deg, var(--blush-light) 0%, var(--blush) 55%, var(--blush-deep) 100%);
  }

  .publisher {
    position: absolute; left: 725px; top: 877px; width: 142px; height: 167px;
    background: var(--white);
    display: flex; flex-direction: column; align-items: center; justify-content: center; gap: 10px;
  }
  .publisher-mark { width: 34px; height: 34px; border-radius: 50%; background: var(--orange); }
  .publisher-name { color: var(--brown); font-weight: 700; font-size: 20px; }

  .author-band {
    position: absolute; left: 0; right: 0; bottom: 0; height: 156px;
    background: var(--brown);
    color: var(--white);
    display: flex; align-items: center; justify-content: space-between;
    padding: 0 86px 0 92px;
  }
  .author-name { font-weight: 900; font-size: 40px; }
  .edition-year { font-weight: 900; font-size: 40px; }
</style>
</head>
<body>
  <main class="cover">
    <header class="title-band">
      <svg width="938" height="411" viewBox="0 0 938 411" aria-labelledby="book-title">
        <rect class="title-rule" x="0" y="352" width="262" height="11" fill="var(--orange)"/>
        <rect class="title-rule" x="676" y="352" width="262" height="11" fill="var(--orange)"/>
        <text id="book-title" x="469" y="318" text-anchor="middle"
              font-family="Cairo, sans-serif" font-weight="900" font-size="160"
              fill="var(--brown)" direction="rtl">الغَيْمُ</text>
      </svg>
    </header>

    <section class="cover-art" role="img" aria-label="صورة يد أب ويد طفل تشكلان معاً قلباً على خلفية وردية دافئة مضيئة"></section>

    <div class="publisher">
      <span class="publisher-mark"></span>
      <span class="publisher-name">دار النخيل</span>
    </div>

    <footer class="author-band">
      <span class="author-name">مازن بن وليد الحمداني</span>
      <bdo class="edition-year" dir="ltr">١٤٤٠-٢٠١٨</bdo>
    </footer>
  </main>
</body>
</html>
```